Black Car Limousine transportation business in Naples Florida

Always stand for my reliability and RVD stands for Love, K and M are the first initials of my children's names. It should show professionalism and a dedication to customer service. We keep our clients identities private. Show our professionalism. We are Black car Black tie company. We service transportation on a reserve basis to and from residents, airports, casinos, hotels,

Target Market(s)

It is a Private car service. High end clients. Businesses, Celebrity and athletes. Service to airports, hotels, special events.

Industry/Entity Type

Business

Contact Information for Business Card

A pearl metallic or Luster card. Standard business card size. Would like the name, Company email, show we take credit cards and phone number. Currently I don't have a website but will like to add later.

Logo Text

STEADFAST RVD TRANSPORTATION

Font styles to use
Serif

Colors
eaeaea
000000

Requirements
Must have
• Must have Company email, show we take credit cards and phone number. Currently I don't have a website but will like to add later.
Nice to have
• Would like to stay with a black and white theme. Open to some color trim.
Should not have
• Open to suggestions

```html
<!DOCTYPE html>
<html lang="en">
<head>
<meta charset="UTF-8">
<title>Steadfast RVD Transportation – Business Card</title>
<link rel="stylesheet" href="https://fonts.googleapis.com/css2?family=Open+Sans:ital,wght@0,400;0,600;0,700;1,700&display=swap">
<style>
  :root {
    --backdrop: #4b4b4b;
    --card: #ffffff;
    --ink: #000000;
    --ink-soft: #444444;
    --silver: #8c8c8c;
    --car-dark: #1a1a1a;
    --car-mid: #5a5a5a;
  }
  * { margin: 0; padding: 0; box-sizing: border-box; }
  html, body {
    width: 1105px; height: 1200px; overflow: hidden;
    background: var(--backdrop);
    font-family: "Open Sans", Arial, sans-serif;
  }
  .card {
    position: absolute; left: 193px; width: 720px; height: 410px;
    background: var(--card);
    overflow: hidden;
  }
  .card--front { top: 167px; }
  .card--back { top: 623px; }

  .logo { position: absolute; display: flex; align-items: center; }
  .logo__vehicle {
    border-radius: 10px 16px 6px 6px;
    background: linear-gradient(180deg, var(--car-mid), var(--car-dark) 60%, #333 100%);
  }
  .logo__name {
    font-weight: 700; color: var(--silver); line-height: 1.05;
    margin-left: 12px;
  }
  .logo__name span { display: block; }
  .logo__line-a { font-size: 19px; letter-spacing: 1px; }
  .logo__line-b { font-size: 46px; letter-spacing: 3px; }
  .logo__line-c { font-size: 15px; letter-spacing: 1.5px; }

  .card--front .logo { left: 52px; top: 68px; }
  .card--front .logo__vehicle { width: 159px; height: 68px; }
  .card--back .logo { left: 137px; top: 150px; }
  .card--back .logo__vehicle { width: 178px; height: 76px; }
  .card--back .logo__line-a { font-size: 21px; }
  .card--back .logo__line-b { font-size: 52px; }
  .card--back .logo__line-c { font-size: 17px; }

  .contacts { position: absolute; left: 53px; top: 280px; list-style: none; }
  .contacts li {
    display: flex; align-items: center; gap: 10px;
    font-size: 18px; color: var(--ink-soft); height: 28px;
  }
  .contacts svg { width: 17px; height: 17px; fill: var(--ink); flex: none; }

  .person { position: absolute; right: 58px; top: 292px; text-align: right; }
  .person__name { font-size: 23px; font-weight: 600; color: var(--ink); letter-spacing: 0.5px; }
  .person__role { font-size: 18px; color: var(--ink-soft); margin-top: 1px; }

  .edge-tab {
    position: absolute; right: 0; top: 293px; width: 17px; height: 51px;
    background: var(--ink);
  }

  .payment {
    position: absolute; left: 0; right: 0; top: 333px;
    display: flex; justify-content: center; align-items: center; gap: 8px;
    font-size: 19px; font-weight: 700; font-style: italic; color: var(--ink);
  }
  .payment svg { width: 26px; height: 20px; }
</style>
</head>
<body>

<section class="card card--front">
  <div class="logo">
    <div class="logo__vehicle" role="img" aria-label="Photo of a black luxury SUV"></div>
    <div class="logo__name">
      <span class="logo__line-a">STEADFAST</span>
      <span class="logo__line-b">RVD</span>
      <span class="logo__line-c">TRANSPORTATION</span>
    </div>
  </div>

  <ul class="contacts">
    <li>
      <svg viewBox="0 0 24 24" aria-hidden="true"><path d="M6.6 10.8a15.1 15.1 0 0 0 6.6 6.6l2.2-2.2a1 1 0 0 1 1-.25 11.4 11.4 0 0 0 3.6.57 1 1 0 0 1 1 1V20a1 1 0 0 1-1 1A17 17 0 0 1 3 4a1 1 0 0 1 1-1h3.5a1 1 0 0 1 1 1c0 1.25.2 2.45.57 3.57a1 1 0 0 1-.25 1z"/></svg>
      239 555 0187
    </li>
    <li>
      <svg viewBox="0 0 24 24" aria-hidden="true"><path d="M2 5h20v14H2z M3.5 6.5l8.5 6.5 8.5-6.5" fill="none" stroke="#000" stroke-width="2"/><path d="M2 5h20v2l-10 7L2 7z"/></svg>
      bookings@steadfastrvd.com
    </li>
    <li>
      <svg viewBox="0 0 24 24" aria-hidden="true"><circle cx="12" cy="12" r="10"/><path d="M7 7c2 0 3 1 3 2.5S8 11 8 13s2 2 2 4M15 5c-1 2 1 3 2 3s2 2 1 4-3 1-3 4" fill="none" stroke="#fff" stroke-width="1.6"/></svg>
      www.steadfastrvd.com
    </li>
  </ul>

  <div class="person">
    <div class="person__name">DANIEL REYES</div>
    <div class="person__role">CEO/Founder</div>
  </div>

  <div class="edge-tab"></div>
</section>

<section class="card card--back">
  <div class="logo">
    <div class="logo__vehicle" role="img" aria-label="Photo of a black luxury SUV"></div>
    <div class="logo__name">
      <span class="logo__line-a">STEADFAST</span>
      <span class="logo__line-b">RVD</span>
      <span class="logo__line-c">TRANSPORTATION</span>
    </div>
  </div>

  <div class="payment">
    <svg viewBox="0 0 26 20" aria-hidden="true">
      <rect x="1" y="2" width="24" height="16" rx="3" fill="#000"/>
      <rect x="1" y="6" width="24" height="3" fill="#fff"/>
      <rect x="5" y="12" width="7" height="3" fill="#fff"/>
    </svg>
    We accept credit cards
  </div>
</section>

</body>
</html>
```